CONTACT US Page and design for website

We need a contact us page for our website. We would like it to have a message area, a map, our information, etc.

Please see the text attachment for what we are looking for. We need to have something that is creative and interesting, modern and professional.

We believe that a contact US page should be very creative because everyone clicks that to contact us. We want it to be super professional, attention grabbing, pleasing to the eye.

PLEASE KEEP THE HEADER AND FOOTER THE SAME, ONLY THE ACTUAL CONTACT US PAGE NEEDS TO BE WORKED ON. THANKS!
We are excited to work with designers for this project.

Target Market(s)

Clients in technology business

Industry/Entity Type

Information Technology

Number of Pages Required

1 page

Font styles to use
Serif

Requirements
Must have
• CHECK THE TEXT ATTACHMENT PLEASE
• Must stay within our design colors and theme.
Nice to have
• see attachment
Should not have
• it should be special

```html
<!DOCTYPE html>
<html lang="en">
<head>
<meta charset="utf-8">
<title>Contact Us – Norvale Tech</title>
<link rel="stylesheet" href="https://fonts.googleapis.com/css2?family=Open+Sans:wght@400;600&family=Poiret+One&family=Arimo:wght@400;700&display=swap">
<style>
:root{
  --teal:#2fb4a3;
  --ink:#111;
  --text:#333;
  --muted:#9a9a9a;
  --line:#d6d6d6;
  --panel:#f2f2f2;
  --footer:#a6a6a6;
  --footer-dark:#8f8f8f;
  --white:#fff;
  --map:#e6e6e2;
}
*{box-sizing:border-box;margin:0;padding:0}
html,body{width:1200px;height:2442px;overflow:hidden;background:var(--white)}
body{position:relative;font-family:"Open Sans",sans-serif;color:var(--text)}
.abs{position:absolute}

/* header */
.account-tab{left:949px;top:0;width:191px;height:33px;background:#a9a9a9;border-radius:0 0 18px 18px;display:flex;justify-content:center;gap:26px;align-items:center;font:11px "Arimo",sans-serif;color:#333}
.account-tab span+span{border-left:1px solid #888;padding-left:14px}
.brand{left:62px;top:28px;display:flex;align-items:center;gap:14px}
.brand-mark{width:40px;height:40px;border-radius:50%;background:var(--teal)}
.brand-name{font:400 34px "Open Sans",sans-serif;color:var(--text);letter-spacing:1px}
.contact-bar{top:52px;display:flex;align-items:center;gap:10px;font:14px "Arimo",sans-serif;color:#555}
.icon-circle{width:34px;height:34px;border-radius:50%;border:1px solid var(--line);display:flex;align-items:center;justify-content:center}
.nav-rule{left:0;width:1200px;height:1px;background:var(--line);top:101px}
.nav-rule.teal{top:148px;background:var(--teal);height:2px}
.main-nav{left:62px;top:116px;display:flex;gap:26px;font:11px "Arimo",sans-serif;color:#333;text-transform:uppercase}
.search{left:931px;top:110px;width:165px;height:33px;border:1px solid #bbb;border-radius:17px;font:11px "Arimo",sans-serif;color:#333;padding:9px 14px}
.search svg{position:absolute;right:12px;top:9px}
.cart{left:1106px;top:109px;width:35px;height:35px;border-radius:50%;border:1px solid #bbb;display:flex;align-items:center;justify-content:center}

/* hero */
.message-panel{left:72px;top:558px;width:1002px;height:718px;background:var(--panel)}
.photo-left{left:268px;top:151px;width:286px;height:487px;background:linear-gradient(90deg,#e2e5e5,#f4f5f5 70%,#d9dddd)}
.photo-right{left:723px;top:151px;width:423px;height:487px;background:linear-gradient(90deg,#eef0ef,#dfe2e1 40%,#f3f4f4)}
.page-title{left:134px;top:452px;font:400 81px/105px "Open Sans",sans-serif;color:var(--ink)}

/* form */
.form-heading{left:143px;top:712px;font:400 45px "Poiret One",sans-serif;color:#222}
.field{left:143px;width:826px;border-bottom:1px solid var(--line);font:11px "Open Sans",sans-serif;color:var(--muted);padding-bottom:6px;text-transform:uppercase}
.submit{left:908px;top:1160px;font:600 17px "Open Sans",sans-serif;color:#333;border-bottom:1px solid #333;line-height:20px}

/* office */
.map{left:433px;top:1302px;width:713px;height:391px;background:var(--map)}
.map-pin{left:757px;top:1466px}
.office-heading{left:282px;top:1357px;font:400 23px "Open Sans",sans-serif;color:#111;letter-spacing:.5px}
.office-rule{left:282px;top:1403px;width:276px;height:3px;background:#111}
.office-address{left:282px;top:1428px;font:400 24px/34px "Open Sans",sans-serif;color:#111;font-style:normal}

/* info panel */
.info-panel{left:103px;top:1644px;width:652px;height:349px;background:var(--panel)}
.section-label{font:600 11px "Open Sans",sans-serif;color:var(--teal);letter-spacing:1px;text-transform:uppercase}
.inquiry{top:1771px;width:152px}
.inquiry h4{font:600 12px "Open Sans",sans-serif;color:#222;padding-bottom:8px;border-bottom:1px solid #ccc;margin-bottom:14px}
.inquiry p{font:12px/20px "Open Sans",sans-serif;color:#333}
.social-row{left:158px;top:1921px;display:flex;gap:18px}
.social-dot{width:20px;height:20px;border-radius:50%;border:2px solid #222}
.hours{left:811px;top:1772px;font:12px/27px "Open Sans",sans-serif;color:#222}
.hours td:first-child{width:95px}
.hours-note{left:811px;top:1926px;width:320px;font:italic 600 12px/27px "Open Sans",sans-serif;color:#222}

/* footer */
.footer{left:0;top:2015px;width:1200px;height:275px;background:var(--footer);color:#fff;font-family:"Arimo",sans-serif}
.footer-about{position:absolute;left:70px;top:17px;width:1060px;text-align:center;font:14px/20px "Arimo",sans-serif}
.footer-rule{position:absolute;left:110px;top:89px;width:980px;height:1px;background:#bdbdbd}
.footer-item{position:absolute;top:107px;font:14px/21px "Arimo",sans-serif;display:flex;gap:12px}
.footer-links{position:absolute;top:183px;font:16px "Arimo",sans-serif}
.support-list{position:absolute;left:955px;top:211px;width:140px;text-align:center;font:bold 10px/14px "Arimo",sans-serif}
.footer-base{left:0;top:2290px;width:1200px;height:152px;background:var(--footer-dark);color:#fff}
.base-circles{position:absolute;left:491px;top:29px;display:flex;gap:20px}
.base-circles span{width:38px;height:38px;border-radius:50%;border:1px solid #c8c8c8}
.base-rule{position:absolute;left:240px;top:80px;width:720px;height:1px;background:#b0b0b0}
.copyright{position:absolute;left:0;width:1200px;top:98px;text-align:center;font:12px/17px "Arimo",sans-serif}
</style>
</head>
<body>

<header>
  <div class="abs account-tab"><span>SIGN UP</span><span>LOGIN</span></div>
  <div class="abs brand"><span class="brand-mark"></span><span class="brand-name">Norvale Tech</span></div>
  <div class="abs contact-bar" style="left:838px">
    <span class="icon-circle"><svg width="16" height="14" viewBox="0 0 16 14"><path d="M2 1h12a1 1 0 0 1 1 1v7a1 1 0 0 1-1 1H7l-4 3v-3H2a1 1 0 0 1-1-1V2a1 1 0 0 1 1-1z" fill="var(--teal)"/></svg></span>
    <span>LIVE CHAT</span>
  </div>
  <div class="abs contact-bar" style="left:974px;font-size:18px;color:#333">
    <span class="icon-circle"><svg width="14" height="14" viewBox="0 0 24 24"><path d="M6.6 10.8a15 15 0 0 0 6.6 6.6l2.2-2.2a1 1 0 0 1 1-.25 11.4 11.4 0 0 0 3.6.57 1 1 0 0 1 1 1V20a1 1 0 0 1-1 1A17 17 0 0 1 3 4a1 1 0 0 1 1-1h3.5a1 1 0 0 1 1 1c0 1.25.2 2.45.57 3.57a1 1 0 0 1-.25 1z" fill="var(--teal)"/></svg></span>
    <span>555-014-3013</span>
  </div>
  <div class="abs nav-rule"></div>
  <nav class="abs main-nav">
    <span>Servers</span><span>Workstations</span><span>Components</span><span>Virtual Reality</span><span>Drones</span><span>About Us</span><span>Blog</span><span>Resources</span><span>Contact Us</span>
  </nav>
  <div class="abs search">Search
    <svg width="14" height="14" viewBox="0 0 14 14"><circle cx="6" cy="6" r="4.5" fill="none" stroke="var(--teal)" stroke-width="2"/><line x1="9.3" y1="9.3" x2="13" y2="13" stroke="var(--teal)" stroke-width="2"/></svg>
  </div>
  <div class="abs cart"><svg width="16" height="14" viewBox="0 0 16 14"><path d="M1 2h2l2 8h8l2-6H4" fill="none" stroke="var(--teal)" stroke-width="2"/><circle cx="6" cy="12.5" r="1.3" fill="var(--teal)"/><circle cx="12" cy="12.5" r="1.3" fill="var(--teal)"/></svg></div>
  <div class="abs nav-rule teal"></div>
</header>

<main>
  <section class="abs message-panel"></section>
  <div class="abs photo-left" role="img" aria-label="Photo of a bright white interior with a hanging fern on a wall shelf"></div>
  <div class="abs photo-right" role="img" aria-label="Photo of a small potted palm tree beside a white wall and window"></div>
  <h1 class="abs page-title">Contact<br>Us</h1>

  <h2 class="abs form-heading">Message center to contact us. Must have:</h2>
  <div class="abs field" style="top:826px">Name</div>
  <div class="abs field" style="top:906px">Email</div>
  <div class="abs field" style="top:986px">Phone Number</div>
  <div class="abs field" style="top:1102px">Message</div>
  <div class="abs submit">SUBMIT</div>

  <div class="abs map" role="img" aria-label="Street map showing the location of the office headquarters"></div>
  <svg class="abs map-pin" width="16" height="24" viewBox="0 0 16 24"><path d="M8 0a8 8 0 0 0-8 8c0 6 8 16 8 16s8-10 8-16a8 8 0 0 0-8-8z" fill="#d32f2f"/><circle cx="8" cy="8" r="3" fill="#8b1a1a"/></svg>
  <h3 class="abs office-heading">OFFICE HEADQUARTERS</h3>
  <div class="abs office-rule"></div>
  <address class="abs office-address">Norvale Tech, LLC.<br>4820 Alder Ave.<br>Westbrook, CA 90210</address>

  <section class="abs info-panel"></section>
  <div class="abs section-label" style="left:158px;top:1729px">Contact Info:</div>
  <div class="abs inquiry" style="left:158px"><h4>General Inquiries</h4><p>(555)014-3013<br>info@norvaletech.com</p></div>
  <div class="abs inquiry" style="left:344px"><h4>Sales Inquiries</h4><p>(555)014-3013<br>sales@norvaletech.com</p></div>
  <div class="abs inquiry" style="left:530px"><h4>Purchasing Inquiries</h4><p>(555)014-3014<br>purchasing@norvaletech.com</p></div>
  <div class="abs section-label" style="left:158px;top:1888px">Stay Connected:</div>
  <div class="abs social-row"><span class="social-dot"></span><span class="social-dot"></span><span class="social-dot"></span><span class="social-dot"></span></div>

  <div class="abs section-label" style="left:811px;top:1731px">Hours of Operation</div>
  <table class="abs hours">
    <tr><td>Monday</td><td>: 8:00am- 5:00pm</td></tr>
    <tr><td>Tuesday</td><td>: 8:00am- 5:00pm</td></tr>
    <tr><td>Wednesday</td><td>: 8:00am- 5:00pm</td></tr>
    <tr><td>Thursday</td><td>: 8:00am- 5:00pm</td></tr>
    <tr><td>Friday</td><td>: 8:00am- 5:00pm</td></tr>
  </table>
  <p class="abs hours-note">Our dedicated customer service representatives are available 24/7 by phone.</p>
</main>

<footer>
  <div class="abs footer">
    <p class="footer-about">Based in Westbrook California, Norvale Tech offers custom servers, storage, and workstations for local businesses in Los Angeles, Beverly Hills, Thousand Oaks, Ventura, Orange County, Santa Barbara, Oxnard, Irvine, Anaheim, and San Diego. Norvale Tech also offers such products to clients throughout the United States and Worldwide.</p>
    <div class="footer-rule"></div>
    <div class="footer-item" style="left:142px">
      <svg width="10" height="14" viewBox="0 0 10 14"><path d="M5 0a5 5 0 0 0-5 5c0 4 5 9 5 9s5-5 5-9a5 5 0 0 0-5-5z" fill="#fff"/><circle cx="5" cy="5" r="1.8" fill="var(--footer)"/></svg>
      <span>4820 Alder Ave.<br>Westbrook, CA 90210</span>
    </div>
    <div class="footer-item" style="left:504px">
      <svg width="12" height="12" viewBox="0 0 24 24" style="margin-top:4px"><path d="M6.6 10.8a15 15 0 0 0 6.6 6.6l2.2-2.2a1 1 0 0 1 1-.25 11.4 11.4 0 0 0 3.6.57 1 1 0 0 1 1 1V20a1 1 0 0 1-1 1A17 17 0 0 1 3 4a1 1 0 0 1 1-1h3.5a1 1 0 0 1 1 1c0 1.25.2 2.45.57 3.57a1 1 0 0 1-.25 1z" fill="#fff"/></svg>
      <span>555-014-3013</span>
    </div>
    <div class="footer-item" style="left:826px">
      <svg width="13" height="10" viewBox="0 0 13 10" style="margin-top:5px"><rect width="13" height="10" fill="#fff"/><path d="M0 0l6.5 5L13 0" fill="none" stroke="var(--footer)" stroke-width="1.2"/></svg>
      <span>sales@norvaletech.com</span>
    </div>
    <span class="footer-links" style="left:102px">Computer Hardware</span>
    <span class="footer-links" style="left:380px">Drones</span>
    <span class="footer-links" style="left:530px">Virtual Reality</span>
    <span class="footer-links" style="left:745px">About Us</span>
    <span class="footer-links" style="left:956px">Customer Support</span>
    <div class="support-list">Terms and Conditions<br>Warranty Information<br>Contact Us<br>Return Policy</div>
  </div>
  <div class="abs footer-base">
    <div class="base-circles"><span></span><span></span><span></span><span></span></div>
    <div class="base-rule"></div>
    <p class="copyright">Norvale Tech, LLC.<br>Copyright © 2017</p>
  </div>
</footer>

</body>
</html>
```